BWP Business Card

A double sided business card based on your "Brindlewood Partners Ltd" Logo. To use the "BWP" logo on 1 side and the full company logo on the reverse.

Detials to be included:

Name: Tomas Wheeler
Postion: Consultant Orthotist & Expert Witness
T: +44 (0) 7700 938271
F: +44 (0) 7654 8820

```html
<!DOCTYPE html>
<html lang="en">
<head>
<meta charset="utf-8">
<title>Brindlewood Partners Ltd – Business Card</title>
<link rel="stylesheet" href="https://fonts.googleapis.com/css2?family=Crimson+Text:wght@400;700&display=swap">
<style>
  :root {
    --navy: #1f3f78;
    --grey: #9a9a9c;
    --grey-light: #c9c9cb;
    --ink-soft: #8a8a8a;
    --paper: #ffffff;
    --block-faint: #e6ebf2;
    --backdrop: #e9e7e3;
  }
  * { box-sizing: border-box; margin: 0; padding: 0; }
  html, body { width: 1200px; height: 720px; overflow: hidden; }
  body {
    background: var(--backdrop);
    font-family: "Crimson Text", Georgia, serif;
    position: relative;
  }
  .card {
    position: absolute;
    top: 205px;
    width: 540px;
    height: 310px;
    background: var(--paper);
    box-shadow: 0 2px 10px rgba(0,0,0,0.12);
    overflow: hidden;
  }
  .card--front { left: 40px; }
  .card--back { left: 620px; }

  .card__swoosh { position: absolute; inset: 0; width: 100%; height: 100%; }

  .brand { position: absolute; left: 28px; top: 30px; display: flex; align-items: center; }
  .brand__mark {
    display: flex; align-items: center; gap: 8px;
    font-weight: 700; font-size: 26px; color: var(--navy);
    padding-right: 16px; margin-right: 16px;
    border-right: 1px solid var(--grey-light);
    height: 60px;
  }
  .brand__square { width: 14px; height: 14px; background: var(--navy); }
  .brand__name {
    font-weight: 700; font-size: 21px; line-height: 1.05; color: var(--navy);
  }

  .person { position: absolute; left: 40px; top: 200px; }
  .person__name { font-weight: 700; font-size: 17px; color: var(--navy); line-height: 1.1; }
  .person__role { font-size: 13px; color: var(--ink-soft); line-height: 1.3; }

  .contact {
    position: absolute; right: 26px; top: 110px;
    color: var(--paper); font-size: 12.5px; text-align: right; line-height: 1.55;
  }
  .contact__line { display: flex; justify-content: flex-end; align-items: center; gap: 6px; }
  .contact__line svg { width: 11px; height: 11px; fill: var(--paper); }
  .contact__line--email { margin-top: 10px; }
  .contact__address { position: absolute; right: 26px; top: 222px; color: var(--paper); font-size: 12.5px; }

  .back-block {
    position: absolute; left: 50%; top: 50%;
    width: 200px; height: 200px;
    transform: translate(-50%, -50%);
    background: var(--block-faint);
  }
  .back-name {
    position: absolute; left: 50%; top: 50%; transform: translate(-50%, -50%);
    width: 420px; text-align: center;
    font-weight: 700; color: var(--navy); font-size: 50px; line-height: 1.0;
  }
  .back-name span { display: block; }
</style>
</head>
<body>

<section class="card card--front" aria-label="Card front">
  <svg class="card__swoosh" viewBox="0 0 540 310" aria-hidden="true">
    <path d="M540,48 C410,70 310,110 240,180 C180,245 110,290 0,292 L0,310 L540,310 Z" fill="var(--grey)"/>
    <path d="M540,60 C415,82 318,120 250,188 C190,252 120,298 0,300 L0,310 L540,310 Z" fill="var(--paper)"/>
    <path d="M540,66 C420,88 325,126 258,193 C198,256 128,302 0,306 L0,310 L540,310 Z" fill="var(--navy)"/>
    <path d="M540,232 C470,240 400,262 330,310" stroke="var(--paper)" stroke-width="1.5" fill="none"/>
  </svg>

  <div class="brand">
    <div class="brand__mark"><span class="brand__square"></span>BWP</div>
    <div class="brand__name">Brindlewood<br>Partners Ltd</div>
  </div>

  <div class="person">
    <div class="person__name">Tomas Wheeler</div>
    <div class="person__role">Consultant Orthotist</div>
    <div class="person__role">Expert Witness</div>
  </div>

  <div class="contact">
    <div class="contact__line">
      <svg viewBox="0 0 12 12"><circle cx="6" cy="6" r="5.5" fill="none" stroke="#fff"/><path d="M4 3.2c.5-.3.9 0 1 .5l.2.8-.6.5c.3.7.8 1.2 1.5 1.5l.5-.6.8.2c.5.1.8.5.5 1-.3.4-.8.6-1.3.5C5 7.3 4.2 6.5 3.8 5 3.6 4.2 3.6 3.6 4 3.2z"/></svg>
      <span>+44 (0) 7700 938271</span>
    </div>
    <div class="contact__line">
      <svg viewBox="0 0 12 12"><rect x="1" y="5" width="10" height="6" rx="1"/><rect x="3" y="1" width="6" height="5" fill="none" stroke="#fff"/></svg>
      <span>+44 (0) 7654 8820</span>
    </div>
    <div class="contact__line contact__line--email">
      <svg viewBox="0 0 12 12"><rect x="0.5" y="2.5" width="11" height="7" rx="1" fill="none" stroke="#fff"/><path d="M1 3l5 3.5L11 3" fill="none" stroke="#fff"/></svg>
      <span>tomas@brindlewoodpartners.co.uk</span>
    </div>
  </div>
  <div class="contact__address">18 Ashcombe Road, Kingston, Surrey, KT2 6QF</div>
</section>

<section class="card card--back" aria-label="Card back">
  <div class="back-block" aria-hidden="true"></div>
  <div class="back-name"><span>Brindlewood</span><span>Partners Ltd</span></div>
</section>

</body>
</html>
```